Employee Benefits and Insurance Consulting

We are an existing company with over 30 years experience but are changing our name. We would like a simple design with grey tones.

Industry/Entity Type

Insurance

Contact Information for Business Card

Marlow Benefits Consulting
Gerald P Hollins CEO
5172 Brackenridge Road
Louisville, TN 37777
gerald@marlowbenefits-example.com
865-412-5593 - O
865-247-3861 - C

```html
<!DOCTYPE html>
<html lang="en">
<head>
<meta charset="utf-8">
<title>Marlow Benefits Consulting – Business Card</title>
<link href="https://fonts.googleapis.com/css2?family=Source+Sans+3:wght@400;600;700&display=swap" rel="stylesheet">
<style>
  :root {
    --teal: #1e9188;
    --grey: #666a6d;
    --white: #ffffff;
    --backdrop: #e9e7e4;
    --card-shadow: rgba(0, 0, 0, 0.18);
  }
  html, body {
    margin: 0;
    padding: 0;
    width: 1200px;
    height: 900px;
    overflow: hidden;
    background: var(--backdrop);
    font-family: "Source Sans 3", "Myriad Pro", Arial, sans-serif;
  }
  .canvas {
    position: relative;
    width: 1200px;
    height: 900px;
  }
  .card {
    position: absolute;
    border-radius: 16px;
    background: var(--white);
    overflow: hidden;
    box-shadow: 0 6px 20px var(--card-shadow);
  }
  .card--front { left: 78px; top: 35px; width: 590px; height: 362px; }
  .card--back { left: 390px; top: 505px; width: 565px; height: 350px; }

  .card__diagonal {
    position: absolute;
    inset: 0;
    width: 100%;
    height: 100%;
  }
  .front__brand {
    position: absolute;
    left: 272px;
    top: 140px;
    transform: translate(-50%, -50%) rotate(-31deg);
    color: var(--teal);
    font-weight: 600;
    font-size: 22px;
    letter-spacing: 1.5px;
    text-transform: uppercase;
    white-space: nowrap;
  }
  .front__details {
    position: absolute;
    right: 36px;
    top: 134px;
    text-align: right;
    color: var(--white);
  }
  .person__name {
    margin: 0;
    font-size: 21px;
    font-weight: 600;
    line-height: 1.2;
  }
  .person__title {
    margin: 2px 0 22px;
    font-size: 15px;
  }
  .address {
    margin: 0 0 16px;
    font-size: 16px;
    line-height: 1.4;
    font-style: normal;
  }
  .contact {
    list-style: none;
    margin: 0;
    padding: 0;
    font-size: 16px;
    line-height: 1.55;
  }
  .contact__item {
    display: flex;
    justify-content: flex-end;
    align-items: center;
    gap: 8px;
  }
  .contact__icon {
    width: 12px;
    height: 12px;
    fill: var(--white);
    flex: none;
  }

  .back__brand {
    position: absolute;
    left: 0;
    right: 0;
    top: 196px;
    text-align: center;
    color: var(--teal);
    font-weight: 600;
    font-size: 30px;
    letter-spacing: 1.5px;
    text-transform: uppercase;
    white-space: nowrap;
  }
</style>
</head>
<body>
<main class="canvas">

  <section class="card card--front" aria-label="Business card front">
    <svg class="card__diagonal" viewBox="0 0 590 362" preserveAspectRatio="none" aria-hidden="true">
      <polygon points="0,354 590,2 590,362 0,362" fill="var(--teal)"/>
      <polygon points="0,346 578,0 590,0 590,8 0,360" fill="var(--grey)"/>
    </svg>

    <div class="front__brand">Marlow Benefits Consulting</div>

    <div class="front__details">
      <h1 class="person__name">Gerald P Hollins</h1>
      <p class="person__title">CEO</p>
      <address class="address">
        5172 Brackenridge Road<br>
        Louisville, TN 37777
      </address>
      <ul class="contact">
        <li class="contact__item">865-247-3861
          <svg class="contact__icon" viewBox="0 0 24 24" aria-label="Office phone"><path d="M6.6 10.8a15.1 15.1 0 0 0 6.6 6.6l2.2-2.2a1 1 0 0 1 1-.25 11.4 11.4 0 0 0 3.6.57 1 1 0 0 1 1 1V20a1 1 0 0 1-1 1A17 17 0 0 1 3 4a1 1 0 0 1 1-1h3.5a1 1 0 0 1 1 1c0 1.25.2 2.45.57 3.57a1 1 0 0 1-.25 1z"/></svg>
        </li>
        <li class="contact__item">865-412-5593
          <svg class="contact__icon" viewBox="0 0 24 24" aria-label="Mobile phone"><path d="M7 1h10a2 2 0 0 1 2 2v18a2 2 0 0 1-2 2H7a2 2 0 0 1-2-2V3a2 2 0 0 1 2-2zm0 3v14h10V4z"/></svg>
        </li>
        <li class="contact__item">gerald@marlowbenefits-example.com
          <svg class="contact__icon" viewBox="0 0 24 24" aria-label="Email"><path d="M2 5h20v14H2zm2 2v.4l8 5 8-5V7zm0 2.8V17h16V9.8l-8 5z"/></svg>
        </li>
      </ul>
    </div>
  </section>

  <section class="card card--back" aria-label="Business card back">
    <div class="back__brand">Marlow Benefits Consulting</div>
  </section>

</main>
</body>
</html>
```